Business Card Design for company

We want new business cards. We'd like something different-- yet still highly professional. Our tagline is Providing leadership, delivering success. Stock photos are ok, as long as they are relevant and look upscale.

Target Market(s)

Architecture/Business Management Consulting/Engineering Consulting

Contact Information for Business Card

dark gray background with pops of blue might be good, but you tell me. You're the designers. Rounded corners might be nice, but again, you tell me.

Font styles to use
Serif
Sans Serif

Colors
3276b5
5c5c5c
9d9d9d
fbfbfb

Requirements
Nice to have
• Something different, but still very professional.

```html
<!DOCTYPE html>
<html lang="en">
<head>
<meta charset="utf-8">
<title>Corvane Advisory – Business Card</title>
<link href="https://fonts.googleapis.com/css2?family=Montserrat:wght@400;500;700&display=swap" rel="stylesheet">
<style>
  :root {
    --backdrop: #2b2b2b;
    --card: #6f6f70;
    --brand-blue: #3276b5;
    --ink-dark: #232323;
    --ink-light: #fbfbfb;
  }
  * { margin: 0; padding: 0; box-sizing: border-box; }
  html, body {
    width: 1200px; height: 900px; overflow: hidden;
    background: var(--backdrop);
    font-family: "Montserrat", sans-serif;
  }
  .stage { position: relative; width: 1200px; height: 900px; }
  .card {
    position: absolute; left: 240px;
    width: 720px; height: 405px;
    background: var(--card);
  }
  .card--front {
    top: 30px;
    display: flex; align-items: center; justify-content: center;
    padding: 0 60px;
  }
  .card--back { top: 465px; }

  .wordmark { font-weight: 700; letter-spacing: 0.02em; line-height: 1.05; white-space: nowrap; }
  .wordmark--front {
    font-size: 48px; color: var(--ink-dark);
    text-align: center;
  }
  .wordmark--back {
    position: absolute; left: 40px; top: 162px;
    font-size: 40px; color: var(--brand-blue);
  }

  .contact {
    position: absolute; left: 372px; top: 50px;
    color: var(--ink-light);
  }
  .contact__name { font-size: 27px; font-weight: 500; letter-spacing: 0.1em; }
  .contact__title { font-size: 15px; letter-spacing: 0.06em; margin-top: 2px; }
  .contact__rule { width: 46px; height: 2px; background: var(--ink-light); margin: 14px 0 12px; }
  .contact__address { font-size: 16px; line-height: 1.45; font-style: normal; letter-spacing: 0.04em; }
  .contact__list { list-style: none; margin-top: 8px; }
  .contact__item {
    display: flex; align-items: center; gap: 16px;
    font-size: 17px; letter-spacing: 0.04em; height: 32px;
    white-space: nowrap;
  }
  .contact__item--plain { padding-left: 36px; }
  .icon { width: 20px; height: 20px; fill: var(--ink-light); flex: none; }
</style>
</head>
<body>
<main class="stage">
  <section class="card card--front" aria-label="Card front">
    <p class="wordmark wordmark--front">CORVANE ADVISORY</p>
  </section>

  <section class="card card--back" aria-label="Card back">
    <p class="wordmark wordmark--back">CORVANE<br>ADVISORY</p>

    <div class="contact">
      <h1 class="contact__name">DANIEL WHITFORD</h1>
      <p class="contact__title">CEO | Founder</p>
      <div class="contact__rule"></div>
      <address class="contact__address">418 Linden Ridge Road,<br>Suite 210 Fairhaven, NY 11790</address>
      <div class="contact__rule"></div>
      <ul class="contact__list">
        <li class="contact__item">
          <svg class="icon" viewBox="0 0 20 20" aria-hidden="true"><path d="M2 7c0-3 4-4 8-4s8 1 8 4v1h-4V6H6v2H2z"/><rect x="4" y="9" width="12" height="8" rx="1"/></svg>
          555-014-2024
        </li>
        <li class="contact__item">
          <svg class="icon" viewBox="0 0 20 20" aria-hidden="true"><rect x="5" y="2" width="10" height="6"/><rect x="2" y="8" width="16" height="10" rx="1"/></svg>
          555-014-2023
        </li>
        <li class="contact__item">
          <svg class="icon" viewBox="0 0 20 20" aria-hidden="true"><path d="M2 4h16v12H2z M3 5l7 6 7-6" fill="none" stroke="#fbfbfb" stroke-width="1.6"/></svg>
          whitford@corvaneadvisory.com
        </li>
        <li class="contact__item">
          <svg class="icon" viewBox="0 0 20 20" aria-hidden="true"><g fill="none" stroke="#fbfbfb" stroke-width="1.6"><circle cx="10" cy="10" r="8"/><ellipse cx="10" cy="10" rx="3.5" ry="8"/><path d="M2 10h16M4 5.5h12M4 14.5h12"/></g></svg>
          www.corvaneadvisory.com
        </li>
        <li class="contact__item contact__item--plain">www.corvaneadvisory.com</li>
      </ul>
    </div>
  </section>
</main>
</body>
</html>
```